Bright Harbor Counseling Letterhead for hip modern business

I would like some ombre use of the colors in the logo hip letterhead that incorporates logo colors and feel, needs to connect with young professionals and college students. i need to be able to write letters to schools to excuse absences as well. i like color blocks on one side preferably using colors from the attached logo design.

Target Market(s)

high income young people, young adults and college students

Industry/Entity Type

mental health

Font styles to use
Serif
Sans Serif

Colors
0054AA
0677BA
7BADD7
CADEEF
E8F1F8
0094D4
00A9DD
6FCCEA
C7EBF8
E9F6FB
00AB8E
00BBA5
67D7C9
C6EFE9
E9F9F6
59FF00
82FF00
B8FF75
E3FFCB
F4FFEA
A7469A
B969AE
D3A5CF
EDDBEB
F8F0F9
6B429C
8869AF
B7A5CE
E3DAEB
F3F0F8

Requirements
Must have
• a modern hip feel, somewhat color

```html
<!DOCTYPE html>
<html lang="en">
<head>
<meta charset="utf-8">
<title>Bright Harbor Counseling — Letterhead</title>
<link href="https://fonts.googleapis.com/css2?family=Jost:wght@300&family=Open+Sans:wght@400;600&family=Lato:wght@400&display=swap" rel="stylesheet">
<style>
  :root {
    --backdrop: #e9e9ea;
    --paper: #ffffff;
    --ink: #3d3d3d;
    --ink-dark: #222222;
    --rule: #1e1e1e;
    --purple: #a7469a;
    --violet: #6b429c;
    --blue: #0677ba;
    --sky: #6fccea;
    --teal: #00bba5;
  }
  * { box-sizing: border-box; margin: 0; padding: 0; }
  html, body {
    width: 1040px; height: 1200px; overflow: hidden;
    background: var(--backdrop);
  }
  .letterhead {
    position: absolute; left: 53px; top: 0;
    width: 934px; height: 1200px;
    background: var(--paper);
    box-shadow: 0 0 18px rgba(0,0,0,0.18);
    font-family: "Open Sans", Arial, sans-serif;
    color: var(--ink);
    overflow: hidden;
  }
  .brand {
    position: absolute; left: 328px; top: 56px; width: 260px;
    font-family: "Jost", "Helvetica Neue", sans-serif;
    font-weight: 300; color: var(--ink-dark);
  }
  .brand-name { display: block; font-size: 36px; line-height: 44px; white-space: nowrap; }
  .brand-sub { display: block; font-size: 20px; letter-spacing: 2.5px; line-height: 24px; }
  .brand-dot {
    position: absolute; left: 532px; top: 10px;
    width: 44px; height: 44px; border-radius: 50%;
    background: var(--violet);
  }
  .letter { position: absolute; left: 89px; width: 754px; font-size: 14.5px; }
  .issue-date { top: 216px; }
  .recipient { top: 253px; line-height: 18px; }
  .salutation { top: 356px; }
  .body { top: 408px; line-height: 27px; }
  .body p { text-align: justify; margin-bottom: 27px; }
  .closing { top: 813px; }
  .signature {
    position: absolute; left: 89px; top: 852px; width: 215px; height: 26px;
    background: linear-gradient(90deg, rgba(60,60,60,0.10), rgba(60,60,60,0.03));
    border-radius: 3px;
  }
  .signer-name { top: 892px; font-size: 18.5px; font-weight: 600; color: var(--ink-dark); }
  .signer-title { top: 923px; }
  .corner-accent { position: absolute; top: 1021px; width: 196px; height: 179px; }
  .corner-accent.left {
    left: 0;
    background: linear-gradient(135deg, rgba(0,148,212,0.55), rgba(107,66,156,0.6) 55%, rgba(167,70,154,0.5));
  }
  .corner-accent.right {
    right: 0;
    background: linear-gradient(225deg, rgba(0,148,212,0.55), rgba(107,66,156,0.6) 55%, rgba(167,70,154,0.5));
  }
  .footer {
    position: absolute; left: 185px; width: 567px; top: 1113px;
    font-family: "Lato", Arial, sans-serif; color: var(--ink-dark);
    text-align: center;
  }
  .footer-address { font-size: 17px; line-height: 24px; padding-bottom: 5px; border-bottom: 1.5px solid var(--rule); }
  .footer-contacts {
    display: flex; justify-content: center; gap: 8px;
    margin: 6px -30px 0; font-size: 16.5px; white-space: nowrap;
  }
  .contact { display: flex; align-items: center; gap: 4px; }
  .contact svg { width: 20px; height: 20px; }
</style>
</head>
<body>
  <main class="letterhead">
    <header class="brand">
      <span class="brand-name">Bright Harbor</span>
      <span class="brand-sub">Counseling</span>
    </header>
    <span class="brand-dot"></span>

    <p class="letter issue-date">Issuing Date: May 5, 2018</p>
    <p class="letter recipient">Name Of Employee Mr. XYZABC<br>Address of Employee<br>Address Line 2 etc..</p>
    <p class="letter salutation">Dear Mr.XYZABC</p>

    <section class="letter body">
      <p>Lorem Ipsum has been the industry's standard dummy text ever since the 1500s, when an unknown printer took a galley of type and scrambled it to make a type specimen book. It has survived not only five centuries, but also the leap into electronic typesetting, remaining essentially unchanged. It was popularised in the 1960s with the release of Dryline sheets containing Lorem Ipsum passages, and more recently with desktop publishing software like Pagewright Studio including versions of Lorem Ipsum.</p>
      <p>Lorem Ipsum is simply dummy text of the printing and typesetting industry. Lorem Ipsum has been the industry's standard dummy text ever since the 1500s, when an unknown printer took a galley of type and scrambled it to make a type specimen book.</p>
      <p>It has survived not only five centuries, but also the leap into electronic typesetting, remaining essentially unchanged. It was popularised in the 1960s with the release of Dryline sheets containing Lorem Ipsum passages.</p>
    </section>

    <p class="letter closing">Yours Sincerely</p>
    <div class="signature" role="img" aria-label="Handwritten signature of Daniel Reyes"></div>
    <p class="letter signer-name">Daniel Reyes</p>
    <p class="letter signer-title">Managing Director</p>

    <div class="corner-accent left" role="img" aria-label="Colour accent in brand purple and blue tones"></div>
    <div class="corner-accent right" role="img" aria-label="Colour accent in brand purple and blue tones"></div>

    <footer class="footer">
      <p class="footer-address">421, Address line goes here Country Name, 45452</p>
      <div class="footer-contacts">
        <span class="contact">
          <svg viewBox="0 0 20 20" aria-hidden="true"><circle cx="10" cy="10" r="9" fill="var(--purple)"/><path d="M7 5.5l2 2-1 1.2c.6 1.3 1.6 2.3 2.9 2.9l1.2-1 2 2-1.3 1.6c-3.5-.3-6.6-3.4-6.9-6.9z" fill="#fff"/></svg>
          044-555 018 246
        </span>
        <span class="contact">
          <svg viewBox="0 0 20 20" aria-hidden="true"><circle cx="10" cy="10" r="9" fill="var(--sky)"/><rect x="5.5" y="6.5" width="9" height="7" rx="1" fill="#fff"/><path d="M5.8 7l4.2 3.3L14.2 7" fill="none" stroke="var(--sky)" stroke-width="1"/></svg>
          hello@brightharbor.example
        </span>
        <span class="contact">
          <svg viewBox="0 0 20 20" aria-hidden="true"><circle cx="10" cy="10" r="9" fill="var(--blue)"/><circle cx="10" cy="10" r="4.5" fill="none" stroke="#fff" stroke-width="1.4"/><path d="M5.5 10h9M10 5.5v9" stroke="#fff" stroke-width="1"/></svg>
          www.brightharbor.example
        </span>
      </div>
    </footer>
  </main>
</body>
</html>
```